Business card design for my company.
I would like the card's background colour to be black. You can also see our web site to get an idea of our brand. https://www.tmwhomecrafting.com.au/
- Name
- Email

```html
<!DOCTYPE html>
<html lang="en">
<head>
<meta charset="utf-8">
<title>TMW Home Crafting – Business Card</title>
<link rel="stylesheet" href="https://fonts.googleapis.com/css2?family=Arimo:wght@400;700&display=swap">
<style>
  :root {
    --backdrop: #e4e4e4;
    --charcoal: #2f2f2f;
    --brand-green: #0b9444;
    --white: #ffffff;
  }
  * { box-sizing: border-box; margin: 0; padding: 0; }
  html, body {
    width: 1200px; height: 1200px; overflow: hidden;
    background: var(--backdrop);
    font-family: "Arimo", Arial, sans-serif;
  }
  .canvas { position: relative; width: 1200px; height: 1200px; }

  .card {
    position: absolute;
    width: 688px; height: 393px;
    display: flex;
    overflow: hidden;
  }
  .card--front { left: 266px; top: 158px; background: var(--white); }
  .card--back  { left: 262px; top: 653px; background: var(--brand-green);
                 align-items: center; justify-content: center; }

  .front__brand {
    width: 380px; height: 100%;
    background: var(--charcoal);
    display: flex; align-items: center; justify-content: center;
  }
  .front__divider { width: 9px; height: 100%; background: var(--white); }
  .front__details {
    flex: 1; height: 100%;
    background: var(--brand-green);
    color: var(--white);
    padding: 92px 0 0 30px;
  }

  .wordmark {
    display: flex; align-items: center; gap: 12px;
    color: var(--white); font-weight: 700;
    letter-spacing: 0.08em; text-transform: uppercase;
  }
  .wordmark__square { width: 18px; height: 18px; background: var(--white); flex: none; }
  .wordmark__name { font-size: 26px; line-height: 1; }
  .card--back .wordmark__name { font-size: 30px; }
  .card--back .wordmark__square { width: 22px; height: 22px; }

  .person__name { font-size: 27px; font-weight: 700; line-height: 1; letter-spacing: 0.01em; }
  .person__role { font-size: 15px; margin-top: 7px; }
  .address { font-size: 16px; line-height: 21px; margin-top: 20px; font-style: normal; }
  .contact-list { list-style: none; margin-top: 14px; }
  .contact-list li {
    display: flex; align-items: center;
    font-size: 16px; height: 20.5px;
  }
  .contact-list svg { width: 14px; height: 14px; margin: 0 11px 0 0; flex: none; fill: var(--white); }
</style>
</head>
<body>
<main class="canvas">

  <section class="card card--front" aria-label="Business card front">
    <div class="front__brand">
      <div class="wordmark">
        <span class="wordmark__square"></span>
        <span class="wordmark__name">TMW Home Crafting</span>
      </div>
    </div>
    <div class="front__divider"></div>
    <div class="front__details">
      <h1 class="person__name">DANIEL HART</h1>
      <p class="person__role">President</p>
      <address class="address">412 Wattle Grove Road<br>Ballarat, VIC 3350</address>
      <ul class="contact-list">
        <li>
          <svg viewBox="0 0 24 24" aria-hidden="true"><path d="M6.6 10.8a15.1 15.1 0 0 0 6.6 6.6l2.2-2.2a1 1 0 0 1 1-.25 11.4 11.4 0 0 0 3.6.57 1 1 0 0 1 1 1V20a1 1 0 0 1-1 1A17 17 0 0 1 3 4a1 1 0 0 1 1-1h3.5a1 1 0 0 1 1 1c0 1.25.2 2.45.57 3.57a1 1 0 0 1-.25 1z"/></svg>
          555-201-4830
        </li>
        <li>
          <svg viewBox="0 0 24 24" aria-hidden="true"><path d="M7 1h10a2 2 0 0 1 2 2v18a2 2 0 0 1-2 2H7a2 2 0 0 1-2-2V3a2 2 0 0 1 2-2zm0 3v15h10V4zm5 16.2a1 1 0 1 0 0 .01z"/></svg>
          555-319-7742
        </li>
        <li>
          <svg viewBox="0 0 24 24" aria-hidden="true"><path d="M2 5h20v14H2zm2 2v.4l8 5.3 8-5.3V7zm0 2.8V17h16V9.8l-8 5.3z"/></svg>
          info@tmwhomecrafting.com
        </li>
        <li>
          <svg viewBox="0 0 24 24" aria-hidden="true"><path d="M12 2a10 10 0 1 0 0 20 10 10 0 0 0 0-20zm-1 17.9A8 8 0 0 1 4.2 10.8L9 15.6v1a2 2 0 0 0 2 2zm6.9-2.5a2 2 0 0 0-1.9-1.4h-1v-3a1 1 0 0 0-1-1H8v-2h2a1 1 0 0 0 1-1V7h2a2 2 0 0 0 2-2v-.4a8 8 0 0 1 2.9 12.8z"/></svg>
          www.tmwhomecrafting.com
        </li>
      </ul>
    </div>
  </section>

  <section class="card card--back" aria-label="Business card back">
    <div class="wordmark">
      <span class="wordmark__square"></span>
      <span class="wordmark__name">TMW Home Crafting</span>
    </div>
  </section>

</main>
</body>
</html>
```